Redesign of business card for Cedar Ridge Mechanical

We are looking for a new design for our business cards for Cedar Ridge Mechanical. We are a plumbing & HVAC construction company, operating on the West Coast of Canada and USA. Logo attached.
Industry/Entity Type
Construction - Plumbing & HVAC
Contact Information for Business Card
Name, address, phone numbers, email, website address
Look and feel
Each slider illustrates characteristics of the customer's brand and the style your logo design should communicate.

```html
<!DOCTYPE html>
<html lang="en">
<head>
<meta charset="UTF-8">
<title>Cedar Ridge Mechanical – Business Card</title>
<link href="https://fonts.googleapis.com/css2?family=Poppins:wght@400;700&display=swap" rel="stylesheet">
<style>
  :root {
    --backdrop: #e4e4e6;
    --ink: #1b1b1b;
    --ink-soft: #3a3a3a;
    --steel-dark: #8e8e90;
    --steel-mid: #b9b9bb;
    --steel-light: #f1f1f2;
    --accent-bar: #1a1a1a;
  }
  * { box-sizing: border-box; margin: 0; padding: 0; }
  html, body {
    width: 1200px; height: 800px; overflow: hidden;
    background: var(--backdrop);
    font-family: "Poppins", sans-serif;
    color: var(--ink);
  }
  .sheet {
    width: 1200px; height: 800px;
    display: flex; align-items: center; justify-content: center; gap: 60px;
  }
  .card {
    position: relative;
    width: 520px; height: 297px;
    background: linear-gradient(115deg,
      var(--steel-mid) 0%, var(--steel-light) 18%, var(--steel-dark) 36%,
      var(--steel-light) 52%, var(--steel-mid) 66%, var(--steel-light) 82%, var(--steel-dark) 100%);
    box-shadow: 0 14px 30px rgba(0,0,0,0.18);
    overflow: hidden;
  }
  .brand {
    position: absolute; top: 26px; left: 28px;
    display: flex; align-items: center; gap: 10px;
  }
  .brand-mark { width: 16px; height: 16px; background: var(--ink); }
  .brand-name {
    font-weight: 700; font-size: 17px; letter-spacing: 0.06em;
    text-transform: uppercase; color: var(--ink);
  }
  /* services side */
  .services {
    position: absolute; right: 30px; bottom: 30px; text-align: right;
  }
  .services-title { font-weight: 700; font-size: 15px; margin-bottom: 6px; }
  .services-list { list-style: none; font-size: 13px; line-height: 1.55; color: var(--ink-soft); }
  /* contact side */
  .contact {
    position: absolute; left: 28px; top: 104px;
    list-style: none; font-size: 13px; line-height: 1.9; color: var(--ink-soft);
  }
  .contact li { display: flex; align-items: center; gap: 8px; }
  .contact svg { width: 12px; height: 12px; fill: none; stroke: var(--ink-soft); stroke-width: 1.6; }
  .person {
    position: absolute; right: 30px; top: 108px; text-align: right;
  }
  .person-name { font-weight: 700; font-size: 16px; letter-spacing: 0.02em; }
  .person-role { font-size: 13px; color: var(--ink-soft); }
  .accent-bar {
    position: absolute; right: 0; top: 106px; width: 12px; height: 46px;
    background: var(--accent-bar);
  }
  .address {
    position: absolute; right: 30px; bottom: 30px; text-align: right;
    font-size: 14px; line-height: 1.5; color: var(--ink);
  }
</style>
</head>
<body>
<main class="sheet">
  <section class="card card-services">
    <div class="brand">
      <span class="brand-mark"></span>
      <span class="brand-name">Cedar Ridge Mechanical</span>
    </div>
    <div class="services">
      <h2 class="services-title">OUR SERVICES</h2>
      <ul class="services-list">
        <li>Pipefitting Systems / Design Build</li>
        <li>Maintenance / Fire Protection / Control Systems</li>
        <li>Energy Recovery &amp; High Efficiency Systems</li>
        <li>Plumbing / HVAC</li>
      </ul>
    </div>
  </section>

  <section class="card card-contact">
    <div class="brand">
      <span class="brand-mark"></span>
      <span class="brand-name">Cedar Ridge Mechanical</span>
    </div>
    <ul class="contact">
      <li>
        <svg viewBox="0 0 12 12"><path d="M3 1.5 L4.8 3.6 L3.8 4.8 Q5 7.2 7.2 8.2 L8.4 7.2 L10.5 9 L9.4 10.5 Q4.6 10.2 1.5 3 Z"/></svg>
        213-555-0148
      </li>
      <li>
        <svg viewBox="0 0 12 12"><rect x="1" y="2.5" width="10" height="7"/><path d="M1 2.5 L6 6.5 L11 2.5"/></svg>
        info@cedarridgemech.com
      </li>
      <li>
        <svg viewBox="0 0 12 12"><circle cx="6" cy="6" r="5"/><ellipse cx="6" cy="6" rx="2.2" ry="5"/><path d="M1 6 H11"/></svg>
        www.cedarridgemech.com
      </li>
    </ul>
    <div class="person">
      <p class="person-name">DANIEL MORROW</p>
      <p class="person-role">President/Founder</p>
    </div>
    <span class="accent-bar"></span>
    <p class="address">2750 Harbor View Rd,<br>Suite #114 Tacoma, WA 98402</p>
  </section>
</main>
</body>
</html>
```